Website Design Chair in Business Administration, especially information and service systems

We, the Chair in Business Administration, especially information and service systems, teach in the field of Business Informatics and Business Administration at Velmont University.
We want to setup our current website in a fresh new and clean design because the design of the old page is outdated: http://dkp.uni-velmont.example/en/
The design should be created in a way that we can integrate it into Wordpress later. Furthermore, the website should have the existing website tabs (pages). We want to add the missing subcategories in the tabs, which means that when you move the mouse over a tab, subcategories/side menus should appear.
We have the goal that the website is very clear and that the students get a direct overview especially of the lectures offered. Furthermore the website should be suitable for mobile devices.
Start page:
In general we are interested in a Tile-based Design (2 or more columns) on the start page - similar to this page: https://www.hochschule-brandor.example/. Here, the fields (Digital Process Networks (DPN) with photo, Lectures of the semester, theses, study projects, projects, current events (social media wall), jobs and internship (together), new publications) should be integrated in the form of tiles with a cover picture per field and a short description.
Furthermore, we would like to position a search bar, a social media wall especially for Instagram (replaces the field current events) and the cooperation partners perhaps as sliders with logos of the companies in the lower part of the start page (see Cooperation tab on the far right) on the start page. Footer remains the same.
Research:
Display the same content more attractively.
Learning-Platform:
Furthermore only as link.
Teaching:
In addition to the existing sub-items (Lectures of the semester, teaching-archive, learning platform, theses and book lending), the "Overview of DPN courses" and the " Open Bachelor & Master theses" should be graphically displayed.
Team:
The concept of the Teamgraph including project connections should remain. Furthermore we can imagine to list the employees with photos and short description in form of tiles (1 employee on a tile) below the graph (2 or more columns of tiles).
Publications:
Continue to display a list of publications.
Jobs and internships:
The Open Positions should be divided here into Research Associates, Student Assistants and interns, so that it becomes clearer (3 columns).
Projects:
Here we are interested a Tile-based Design (2 or more columns). We want to integrate the project fields (KORUVAN, Tidal Record Vault etc.) in the form of tiles with a title image per field and a short description.
Events and cooperations should be removed as they are sufficiently represented on the start page.
Target Market(s)
Students as well as current and future project partners
Logo Text
DPN (+ optional Chair in Digital Process Networks)
Coding
Coded - Design and coding required
Number of Pages Required
5+ page
Requirements
Must have
- See description above
Nice to have
- Perhaps a design can be created in which a direct connection to research content (AI, Deep Learning etc.) and to courses (Data Science, AI in companies etc.) can be seen.

```html
<!DOCTYPE html>
<html lang="en">
<head>
<meta charset="utf-8">
<title>Digital Process Networks – Website Design</title>
<link href="https://fonts.googleapis.com/css2?family=Fira+Sans:wght@500;600&family=Montserrat:wght@600;700;800&family=Nunito+Sans:wght@400;600;700&display=swap" rel="stylesheet">
<style>
:root{
  --board:#2b2b2b;
  --navy:#1b2a5c;
  --footer:#13244f;
  --orange:#e8441f;
  --blush:#f4f1f3;
  --grey:#ececef;
  --ink:#3a3f4e;
  --line:#d9d9df;
  --white:#ffffff;
}
*{box-sizing:border-box;margin:0;padding:0}
html,body{width:695px;height:1200px;overflow:hidden;background:var(--board)}
body{position:relative;font-family:"Nunito Sans",sans-serif;color:var(--ink)}
.page{position:absolute;top:26px;width:644px;background:var(--white);transform:scale(0.4767);transform-origin:0 0;overflow:hidden}
.page--home{left:34px;height:2390px}
.page--research{left:355px;height:926px}
.photo{position:absolute}

.masthead{position:absolute;left:0;top:0;width:644px;height:36px;border-bottom:1px solid var(--line)}
.masthead__brand{position:absolute;left:71px;top:10px;font:600 12.5px "Fira Sans",sans-serif;color:var(--navy)}
.masthead__follow{position:absolute;left:488px;top:12px;font:600 5px "Montserrat",sans-serif;color:var(--navy);letter-spacing:.3px}
.masthead__dots{position:absolute;left:519px;top:8px;display:flex;gap:4px}
.masthead__dots span{width:15px;height:15px;border-radius:50%;background:#2c5bc6}
.masthead__dots span:nth-child(2){background:#2a9fe6}
.masthead__dots span:nth-child(3){background:var(--navy)}
.mainnav{position:absolute;left:71px;top:43px;display:flex;font:600 6.6px "Montserrat",sans-serif;color:var(--navy);letter-spacing:.2px}
.mainnav span{margin-right:15.5px}
.mainnav .is-active{color:var(--orange)}

.btn{position:absolute;background:var(--orange);color:var(--white);font:700 6.5px "Montserrat",sans-serif;display:flex;align-items:center;justify-content:center;letter-spacing:.3px}
.sec-title{position:absolute;font:700 12px "Montserrat",sans-serif;color:var(--navy);letter-spacing:.2px;text-align:center}
.sec-title::after{content:"";display:block;width:26px;height:1.5px;background:var(--navy);margin:7px auto 0}
.sec-title--left{text-align:left}
.sec-title--left::after{margin-left:0}

.hero__title{position:absolute;left:0;width:644px;top:96px;text-align:center;font:700 16px "Montserrat",sans-serif;color:var(--white);text-shadow:0 1px 3px rgba(0,0,0,.4)}
.hero__dots{position:absolute;left:302px;top:318px;display:flex;gap:5px}
.hero__dots span{width:4px;height:4px;border-radius:50%;background:var(--white)}
.hero__dots .on{background:var(--orange);outline:1px solid #fff}

.partners{position:absolute;left:0;top:342px;width:644px;height:63px;display:flex;align-items:center;justify-content:center;gap:34px;font:700 10px "Montserrat",sans-serif;color:#222}
.partners .arrow{font:400 14px "Nunito Sans",sans-serif;color:#888}

.about{position:absolute;left:0;top:405px;width:644px;height:255px;background:var(--blush)}
.about__text{position:absolute;left:341px;top:80px;width:232px;font-size:6.3px;line-height:1.72}

.lecture{position:absolute;top:732px;width:121px;height:120px;border:1px solid #9aa0b4;text-align:center}
.lecture svg{position:absolute;left:41px;top:16px}
.lecture p{position:absolute;left:0;right:0;top:70px;font:600 6px "Montserrat",sans-serif;color:var(--navy);line-height:1.4;text-transform:uppercase}

.theses{position:absolute;left:0;top:885px;width:310px;height:261px;background:var(--blush)}
.theses h3{position:absolute;left:71px;top:24px;font:700 7.5px "Montserrat",sans-serif;color:var(--navy)}
.theses h3::after{content:"";display:block;width:30px;height:1.2px;background:var(--navy);margin-top:3px}
.theses .lead{position:absolute;left:71px;top:50px;width:210px;font-size:6.3px;line-height:1.7}
.ticks{position:absolute;left:71px;top:116px;list-style:none;font-size:6.3px;line-height:2.07}
.ticks li{padding-left:12px;position:relative}
.ticks li::before{content:"";position:absolute;left:1px;top:3px;width:5px;height:2.5px;border-left:1.3px solid var(--orange);border-bottom:1.3px solid var(--orange);transform:rotate(-45deg)}

.tile{position:absolute;width:162px;height:120px}
.tile span{position:absolute;left:9px;bottom:6px;font:700 8px "Montserrat",sans-serif;color:var(--white)}
.tile span::before{content:"";position:absolute;left:0;top:-5px;width:12px;height:1.2px;background:#fff}
.tile i{position:absolute;right:4px;bottom:4px;width:12px;height:12px;background:var(--orange)}
.tile i::after{content:"";position:absolute;left:3px;top:3.5px;width:4px;height:4px;border-right:1.3px solid #fff;border-top:1.3px solid #fff;transform:rotate(45deg)}

.events{position:absolute;left:0;top:1495px;width:644px;height:210px;background:var(--blush)}
.event{position:absolute;top:65px;width:123px;height:123px}
.event span{position:absolute;left:8px;bottom:7px;font:700 5.6px "Montserrat",sans-serif;color:#fff;line-height:1.3;text-transform:uppercase}
.ev-arrow{position:absolute;top:112px;width:11px;height:16px;background:#fff;font:700 9px "Nunito Sans",sans-serif;color:#333;display:flex;align-items:center;justify-content:center}

.pubs{position:absolute;left:0;top:1705px;width:644px;height:208px;background:var(--grey)}
.pub{position:absolute;top:65px;width:161px;height:122px;background:var(--white);padding:15px 18px}
.pub b{display:block;font:700 6.4px "Montserrat",sans-serif;color:var(--navy);margin-bottom:5px}
.pub p{font-size:5.8px;line-height:1.6}
.pub em{position:absolute;left:20px;top:94px;font-style:normal;font-size:5px;border:1px solid #bbb;padding:2px 5px}

.jobs h3{position:absolute;left:354px;top:1947px;font:700 11px "Montserrat",sans-serif;color:var(--navy)}
.jobs .sub{position:absolute;left:354px;top:1967px;width:200px;font:600 6.4px "Montserrat",sans-serif;color:var(--navy);line-height:1.5}
.job{position:absolute;left:355px;width:218px;background:var(--blush);font-size:6.8px;line-height:1.5;padding:0 14px;display:flex;align-items:center}

.footer{position:absolute;left:0;width:644px;height:190px;background:var(--footer);color:#fff}
.footer__brand{position:absolute;left:81px;top:45px;font:600 15px "Fira Sans",sans-serif;line-height:1.55}
.footer__rule{position:absolute;left:249px;top:27px;width:1px;height:88px;background:rgba(255,255,255,.2)}
.footer h4{position:absolute;top:27px;font:700 6.2px "Montserrat",sans-serif;letter-spacing:.3px}
.footer__menu{position:absolute;top:46px;font-size:6px;line-height:1.8;text-transform:uppercase;list-style:none}
.social{position:absolute;left:516px;display:flex;align-items:center;gap:7px;font-size:5.8px;line-height:1.3}
.social i{width:12px;height:12px;border-radius:50%;background:#fff;flex:none}
.footer__line{position:absolute;left:71px;top:144px;width:502px;height:1px;background:rgba(255,255,255,.15)}
.footer__copy{position:absolute;left:0;right:0;top:166px;text-align:center;font-size:4.6px;color:#c9cfdf}

.r-hero__title{position:absolute;left:0;width:644px;top:146px;text-align:center;font:800 16px "Montserrat",sans-serif;color:#fff}
.r-head{position:absolute;left:71px;font:800 11.5px "Montserrat",sans-serif;color:var(--navy)}
.r-tile{position:absolute;width:160px;height:128px}
.r-cap{position:absolute;width:160px;text-align:center;font:700 6.2px "Montserrat",sans-serif;color:var(--navy);line-height:1.45}
</style>
</head>
<body>

<section class="page page--home">
  <header class="masthead">
    <div class="masthead__brand">Digital Process Networks</div>
    <div class="masthead__follow">FOLLOW</div>
    <div class="masthead__dots"><span></span><span></span><span></span></div>
  </header>
  <nav class="mainnav"><span>RESEARCH</span><span>LEARNING-PLATFORM</span><span>TEACHING</span><span>TEAM</span><span>PUBLICATIONS</span><span>JOBS</span><span>PROJECTS</span><span>EVENTS</span><span>COOPERATIONS</span></nav>

  <div class="photo" role="img" aria-label="Audience in a lecture hall listening to a speaker" style="left:0;top:62px;width:644px;height:280px;background:linear-gradient(180deg,#8d8f93 0%,#6b6663 45%,#3d3532 100%)"></div>
  <div class="hero__title">Digital Process Networks</div>
  <div class="btn" style="left:283px;top:130px;width:77px;height:22px;font-size:8px">READ MORE</div>
  <div class="hero__dots"><span></span><span></span><span class="on"></span><span></span><span></span></div>

  <div class="partners">
    <span class="arrow">‹</span><span>NORVELLA</span><span>Brightpath</span><span>Linqora</span><span>Harlow Academy</span><span style="font-size:8px;letter-spacing:1px">CALDER MARINE</span><span class="arrow">›</span>
  </div>

  <div class="about">
    <div class="photo" role="img" aria-label="Seminar room with participants watching a presentation" style="left:74px;top:30px;width:188px;height:126px;background:linear-gradient(135deg,#9a8f7a,#5c6a4e)"></div>
    <div class="photo" role="img" aria-label="Workshop around a long conference table" style="left:125px;top:100px;width:188px;height:127px;background:linear-gradient(135deg,#b9b8b0,#6d6656);border:1px solid #fff"></div>
    <div class="sec-title sec-title--left" style="left:341px;top:23px;line-height:1.45;font-size:11px">DIGITAL PROCESS<br>NETWORKS (DPN)</div>
    <p class="about__text">Chair in Business Administration, especially Digital Process Networks at Velmont University deals with the development and management of data-driven services, for instance healthcare. Directed by Prof. Dr.-Ing. Lukas Brenner, the chair investigates how the application of experimental design methods combined with distributed, data analytic approaches lead to adaptive service designs and innovative solutions. This research is conducted in basic and applied research projects in cooperation with leading research and industry partners. Results are applied and validated in industry projects by the research group Adaptive Service Design (ASD) at the Institute for Applied Machine Cognition (IAMC).</p>
    <div class="btn" style="left:343px;top:213px;width:57px;height:16px">READ MORE</div>
  </div>

  <div class="sec-title" style="left:0;width:644px;top:688px">LECTURES OF THE SEMESTER</div>
  <div class="lecture" style="left:70px">
    <svg width="38" height="38" viewBox="0 0 38 38"><circle cx="19" cy="19" r="13" fill="none" stroke="#1b2a5c" stroke-width="6" stroke-dasharray="5 3.2"/><circle cx="19" cy="19" r="10" fill="#1b2a5c"/><circle cx="19" cy="16" r="2.4" fill="#fff"/><path d="M14 24a5 4 0 0 1 10 0z" fill="#fff"/></svg>
    <p>Service<br>Management</p></div>
  <div class="lecture" style="left:199px">
    <svg width="38" height="38" viewBox="0 0 38 38"><rect x="5" y="8" width="24" height="24" rx="3" fill="none" stroke="#1b2a5c" stroke-width="3.2"/><path d="M14 24l2-6 12-12 4 4-12 12z" fill="#1b2a5c"/></svg>
    <p>AI in<br>Companies</p></div>
  <div class="lecture" style="left:326px">
    <svg width="38" height="38" viewBox="0 0 38 38"><path d="M10 34v-8c-4-3-5-8-3-13 3-7 13-9 19-4 3 3 4 6 3 10l3 5h-3v4c0 2-2 3-4 3h-3v3z" fill="#1b2a5c"/><circle cx="18" cy="15" r="5" fill="none" stroke="#fff" stroke-width="2.4" stroke-dasharray="2.5 1.5"/></svg>
    <p>Service<br>Engineering</p></div>
  <div class="lecture" style="left:453px">
    <svg width="38" height="38" viewBox="0 0 38 38"><rect x="14" y="6" width="20" height="14" fill="none" stroke="#1b2a5c" stroke-width="2.4"/><path d="M24 20v12M20 32l4-8 4 8" stroke="#1b2a5c" stroke-width="2" fill="none"/><circle cx="8" cy="10" r="3" fill="#1b2a5c"/><path d="M4 15h7l6 4-1 2-5-2v15H8v-8H6v8H3z" fill="#1b2a5c"/></svg>
    <p>Seminar "Pandemic<br>Monitoring Systems<br>and Mobile Apps"</p></div>

  <div class="theses">
    <h3>THESES</h3>
    <p class="lead">There are three subject areas available for the editing of theses (Bachelor/Master), projects and internships: (1) Service Design and Management, (2) Data-driven Services, and (3) Conceptual Modeling. Please, submit your application for theses (Bachelor/Master), projects and internships here.</p>
    <ul class="ticks">
      <li>Smart Services</li><li>Business models in healthcare, e.g., VitaTrack Kit</li><li>Information systems for health records</li><li>Telematik</li><li>Apps in healthcare</li><li>Adoption of Smart Home Services</li><li>Processing user motives in HCI settings</li>
    </ul>
    <div class="btn" style="left:71px;top:221px;width:57px;height:16px">READ MORE</div>
  </div>
  <div class="photo" role="img" aria-label="Speaker presenting to a seated audience in a library hall" style="left:310px;top:885px;width:334px;height:261px;background:linear-gradient(160deg,#6f8aa0 0%,#5a4a3c 50%,#2d2623 100%)"></div>

  <div class="sec-title" style="left:0;width:624px;top:1173px">OUR PROJECTS</div>
  <div class="tile photo" role="img" aria-label="Project meeting in a conference room" style="left:61px;top:1214px;background:linear-gradient(160deg,#b4b2a8,#5f5c54)"><span>KORUVAN</span><i></i></div>
  <div class="tile photo" role="img" aria-label="Person in front of a wall of data network graphics" style="left:231px;top:1214px;background:linear-gradient(160deg,#c9ced6,#7d8796)"><span>TIDAL RECORD VAULT</span><i></i></div>
  <div class="tile photo" role="img" aria-label="Busy shopping mall seen from above" style="left:401px;top:1214px;background:linear-gradient(160deg,#a08a78,#5c5048)"><span>LUMERIS</span><i></i></div>
  <div class="tile photo" role="img" aria-label="Tractor working a field" style="left:61px;top:1342px;background:linear-gradient(180deg,#8696a6,#4d5a3e)"><span>GREENFIELD LINK</span><i></i></div>
  <div class="tile photo" role="img" aria-label="Container port at night" style="left:231px;top:1342px;background:linear-gradient(180deg,#2f3f63,#6a3c3a)"><span>QUANTRA</span><i></i></div>
  <div class="tile photo" role="img" aria-label="Hands typing on a laptop with security graphics" style="left:401px;top:1342px;background:linear-gradient(160deg,#5d7187,#1f2f45)"><span>SOLVIKA</span><i></i></div>

  <div class="events">
    <div class="sec-title" style="left:0;width:624px;top:20px">CURRENT EVENTS</div>
    <div class="event photo" role="img" aria-label="Consortium meeting around tables" style="left:5px;background:linear-gradient(180deg,#b3b0a8,#4a4640)"><span>KORUVAN Consortial<br>Meeting</span></div>
    <div class="event photo" role="img" aria-label="Workshop in a room with green curtains" style="left:132px;background:linear-gradient(180deg,#7b8a5a,#3d3a33)"><span>KORUVAN AP 2<br>Workshop</span></div>
    <div class="event photo" role="img" aria-label="Group photo of project partners" style="left:259px;background:linear-gradient(180deg,#a4a5a2,#3a3a3e)"><span>Projekt Tidal<br>Record Vault</span></div>
    <div class="event photo" role="img" aria-label="Group photo in front of a blue backdrop" style="left:386px;background:linear-gradient(180deg,#5b7ab0,#3a3d48)"><span>KORUVAN Consortial<br>Meeting</span></div>
    <div class="event photo" role="img" aria-label="Group photo at a summit stage" style="left:513px;background:linear-gradient(180deg,#d6d8de,#3a3436)"><span>KORUVAN AP 2<br>Workshop</span></div>
    <div class="ev-arrow" style="left:5px">‹</div>
    <div class="ev-arrow" style="left:628px">›</div>
  </div>

  <div class="pubs">
    <div class="sec-title" style="left:0;width:644px;top:23px">PUBLICATIONS</div>
    <div class="pub" style="left:72px"><b>Varga, E., &amp; Brenner, L.</b><p>A Situation-Specific Smart Retail Service Based On Vital Signs, Proceedings of the 41th Annual Meeting on Service Data Design, 2020.</p><em>PDF (3.62 MB)</em></div>
    <div class="pub" style="left:242px"><b>Varga, E., &amp; Brenner, L.</b><p>Data-Driven System for Treatment of Obese Children in Rural Areas, MobiCare '20 Workshop: Learning from mHealth Success Stories: Effective Interventions for Marginalised Populations, 2020.</p><em>PDF (3.62 MB)</em></div>
    <div class="pub" style="left:412px"><b>Lind, T.; Orban, K.; Fessler, M. &amp; Brenner, L.</b><p>CD2 : Combined Distances of Contrast Distributions for the Assessment of Perceptual Quality of Image Processing, POSTER presentation at VDSC'20, 2019.</p><em>PDF (3.62 MB)</em></div>
  </div>

  <div class="jobs">
    <div class="photo" role="img" aria-label="Speaker at a lectern in a brick hall with blue lighting" style="left:10px;top:1927px;width:314px;height:261px;background:linear-gradient(160deg,#6b5f66 0%,#3d3a68 55%,#1e1b24 100%)"></div>
    <h3>JOBS AND INTERNSHIP</h3>
    <p class="sub">GAIN PRACTICAL EXPERIENCE IN AN INTERNSHIP<br>WITH US –BECOME A MEMBER OF THE TEAM!</p>
    <div class="job" style="top:2000px;height:43px">VU: Research Assistant to support Project Management wanted!</div>
    <div class="job" style="top:2049px;height:43px">IAMC: Student assistant in the field of PR and Communication wanted!</div>
    <div class="job" style="top:2100px;height:30px">VU: Research Assistant wanted!</div>
    <div class="btn" style="left:355px;top:2148px;width:73px;height:20px;font-size:7.5px">APPLY JOB</div>
  </div>

  <footer class="footer" style="top:2200px">
    <div class="footer__brand">Digital Process<br>Networks</div>
    <div class="footer__rule"></div>
    <h4 style="left:307px">MENU</h4>
    <ul class="footer__menu" style="left:307px"><li>Research</li><li>Learning-Platform</li><li>Teaching</li><li>Team</li><li>Publications</li></ul>
    <ul class="footer__menu" style="left:401px"><li>Jobs</li><li>Projects</li><li>Events</li><li>Cooperations</li></ul>
    <h4 style="left:516px">FOLLOW US</h4>
    <div class="social" style="top:48px"><i></i><span>Like us on<br>FRONTPAGE</span></div>
    <div class="social" style="top:75px"><i></i><span>Follow us on<br>CHIRPER</span></div>
    <div class="social" style="top:102px"><i></i><span>Follow us on<br>WORKLINE</span></div>
    <div class="footer__line"></div>
    <div class="footer__copy">Copyright © 2020 All Rights Reserved</div>
  </footer>
</section>

<section class="page page--research">
  <header class="masthead">
    <div class="masthead__brand">Digital Process Networks</div>
    <div class="masthead__follow">FOLLOW</div>
    <div class="masthead__dots"><span></span><span></span><span></span></div>
  </header>
  <nav class="mainnav"><span class="is-active">RESEARCH</span><span>LEARNING-PLATFORM</span><span>TEACHING</span><span>TEAM</span><span>PUBLICATIONS</span><span>JOBS</span><span>PROJECTS</span><span>EVENTS</span><span>COOPERATIONS</span></nav>

  <div class="photo" role="img" aria-label="Hands typing on a laptop at a desk" style="left:0;top:62px;width:644px;height:223px;background:linear-gradient(135deg,#5a5f6c 0%,#7d7f86 50%,#b8b7b4 100%)"></div>
  <div class="r-hero__title">RESEARCH</div>

  <div class="r-head" style="top:309px">MANAGEMENT</div>
  <div class="r-tile photo" role="img" aria-label="Business handshake over a desk" style="left:71px;top:337px;background:linear-gradient(160deg,#9a9690,#3c3a3b)"></div>
  <div class="r-tile photo" role="img" aria-label="Hands working on a laptop with charts" style="left:242px;top:337px;background:linear-gradient(160deg,#aeb2b8,#4c525a)"></div>
  <div class="r-tile photo" role="img" aria-label="Training session in a brick-walled room" style="left:413px;top:337px;background:linear-gradient(160deg,#b0aaa4,#5d5550)"></div>
  <div class="r-cap" style="left:71px;top:476px">INNOVATIVE BUSINESS MODELS<br>USING AI TECHNOLOGIES</div>
  <div class="r-cap" style="left:242px;top:476px">HYBRID VALUE CREATION AND AI</div>
  <div class="r-cap" style="left:413px;top:476px">TRANSFER OF SKILLS AND<br>KNOWLEDGE</div>

  <div class="r-head" style="top:523px">TECHNOLOGIES</div>
  <div class="r-tile photo" role="img" aria-label="Globe with glowing network connections" style="left:71px;top:550px;background:radial-gradient(circle at 45% 55%,#3e6fae,#0a1630 75%)"></div>
  <div class="r-tile photo" role="img" aria-label="Students in a bright seminar room" style="left:242px;top:550px;background:linear-gradient(160deg,#e4e3e0,#a89a8c)"></div>
  <div class="r-tile photo" role="img" aria-label="Audience at a presentation in a library" style="left:413px;top:550px;background:linear-gradient(160deg,#6b93b8,#3a2f2a)"></div>
  <div class="r-cap" style="left:71px;top:689px">AI OPERATING SYSTEM FOR<br>INTERNET OF THINGS (AIOS – IOT)</div>
  <div class="r-cap" style="left:242px;top:689px">DEEP LEARNING AND PATTERN<br>RECOGNITION IN SENSOR DATA STREAMS</div>
  <div class="r-cap" style="left:413px;top:689px">RESPONSIBLE AI IN USER<br>INTER FACES</div>

  <footer class="footer" style="top:742px;height:184px">
    <div class="footer__brand">Digital Process<br>Networks</div>
    <div class="footer__rule"></div>
    <h4 style="left:307px">MENU</h4>
    <ul class="footer__menu" style="left:307px"><li>Research</li><li>Learning-Platform</li><li>Teaching</li><li>Team</li><li>Publications</li></ul>
    <ul class="footer__menu" style="left:401px"><li>Jobs</li><li>Projects</li><li>Events</li><li>Cooperations</li></ul>
    <h4 style="left:516px">FOLLOW US</h4>
    <div class="social" style="top:48px"><i></i><span>Like us on<br>FRONTPAGE</span></div>
    <div class="social" style="top:75px"><i></i><span>Follow us on<br>CHIRPER</span></div>
    <div class="social" style="top:102px"><i></i><span>Follow us on<br>WORKLINE</span></div>
    <div class="footer__line"></div>
    <div class="footer__copy">Copyright © 2020 All Rights Reserved</div>
  </footer>
</section>

</body>
</html>
```